Form Sculptors Business Card

Professional cosmetic surgery company, based in very exclusive area in London. High profiled clientele. Brand is very artistic, modern, state-of-the-art, safe. The best in the business. Celebrity clientele.

Form Sculptor’s of London is a brand serving a discriminating and exclusive clientele who value personal service that is both intimate and high end. Our clients choose Form Sculptors because of the relationships we share with all of our customers. The clients of Form Sculptors have an equal partnership between customers, and very experienced, highly qualified medical professionals. This together provides you with a professional service that keeps you looking good and feeling good. It is a relationship based on honesty, compassion, loyalty and respect.
Form Sculptor’s have provided services for internationally recognised celebrities, and other high profiled individuals.

The cards are used for networking at private, exclusive events with VIPs.

Target Market(s)

Professionals
Rich people

Industry/Entity Type

Professional Service

Contact Information for Business Card

Need double sided business card design for 4 people. Back of the business card needs to have contrast background to the front with butterfly watermark with services provided:
Hair Restoration surgery
Hair Loss treatments
Breast surgery
Rhinoplasty
Pulvix Liposuction
Fat Grafting
Lumaxin & Fillers

Front of the business card needs to be a nice satin black.
with following information:
Calvert Osterlund - name
Chief Executive - Job title

www.formsculptors-example.co.uk
calvert@formsculptors-example.co.uk
Phone: +44 (0)207 946 0321
Mobile: +44 (0)7700 900 147

Farrowmere Clinic
14 Farrowmere Lane | London | W1X 4QP
Off Quenby Street

All business cards have the same address, phone, website as Calvert's details.
Same details on the back of the business card as well.
The other cards have different name, job title, email, mobile number

Teodor Lunn - Name
Partner - Job Title
Former England International Cricketer - please include below job title

email: teodor@formsculptors-example.co.uk
mobile: +44(0)7700 900582

Dr Castello Vranesk - Name
Plastic Surgeon - Job Title
drvranesk@formsculptors-example.co.uk
No mobile number

Dr Ezra Tolquist FRCS (please put FRCS in small font) - Name
Hair Restoration Surgeon - Job Title
drtolquist@formsculptors-example.co.uk
No mobile number

Colors
cedeec
85abd2
0655a3

Requirements
Must have
• The logo needs to be in a metallic finish
• Text needs to be striking
• nice background
• butterfly watermark on the back

```html
<!DOCTYPE html>
<html lang="en">
<head>
<meta charset="utf-8">
<title>Form Sculptors Business Card</title>
<link rel="stylesheet" href="https://fonts.googleapis.com/css2?family=Open+Sans:wght@300;400;600;700&display=swap">
<style>
  :root {
    --page: #d6d6d8;
    --card: #3a393c;
    --tile-dark: #545357;
    --tile-blue: #1f8bcf;
    --band-dark: #4a494c;
    --band-light: #d8d8da;
    --white: #ffffff;
    --brand-blue: #0655a3;
    --brand-soft: #85abd2;
  }
  * { box-sizing: border-box; margin: 0; padding: 0; }
  html, body { width: 1000px; height: 1200px; overflow: hidden; }
  body {
    background: var(--page);
    font-family: "Open Sans", Arial, sans-serif;
    color: var(--white);
    position: relative;
  }
  .card {
    position: absolute;
    left: 60px;
    width: 880px;
    height: 530px;
    background: var(--card);
  }
  .card--front { top: 50px; }
  .card--back { top: 620px; }

  .tile {
    position: absolute;
    padding: 14px 16px;
    text-align: right;
  }
  .tile--dark { background: var(--tile-dark); }
  .tile--blue { background: var(--tile-blue); }
  .tile__icon { position: absolute; top: 16px; right: 16px; width: 34px; height: 34px; fill: var(--white); }
  .tile__icon--stroke { fill: none; stroke: var(--white); stroke-width: 2.4; stroke-linejoin: round; stroke-linecap: round; }

  .tile--logo { left: 59px; top: 60px; width: 336px; height: 197px; display: flex; align-items: center; justify-content: center; gap: 12px; }
  .tile--name { left: 411px; top: 60px; width: 197px; height: 197px; }
  .tile--title { left: 624px; top: 60px; width: 197px; height: 197px; }
  .tile--info { left: 59px; top: 273px; width: 336px; height: 197px; }
  .tile--address { left: 411px; top: 273px; width: 197px; height: 197px; }
  .tile--phone { left: 624px; top: 273px; width: 197px; height: 197px; }

  .brand-mark { width: 16px; height: 16px; border-radius: 50%; background: var(--brand-soft); }
  .brand-name { font-size: 30px; font-weight: 400; letter-spacing: 1px; color: var(--brand-soft); text-transform: uppercase; }

  .person__first { position: absolute; right: 16px; top: 86px; font-size: 36px; font-weight: 700; line-height: 1; }
  .person__last { position: absolute; right: 16px; top: 130px; font-size: 27px; font-weight: 300; line-height: 1; }
  .job-title { position: absolute; right: 16px; top: 100px; font-size: 15px; line-height: 1.35; text-transform: uppercase; }

  .info__heading { position: absolute; right: 16px; top: 92px; font-size: 40px; font-weight: 300; line-height: 1; }
  .info__lines { position: absolute; right: 16px; top: 144px; font-size: 12.5px; line-height: 1.6; text-transform: uppercase; }

  .address__heading { position: absolute; right: 14px; top: 98px; font-size: 22px; font-weight: 700; line-height: 1; white-space: nowrap; }
  .address__lines { position: absolute; right: 14px; top: 132px; font-size: 14px; line-height: 1.6; text-transform: uppercase; white-space: nowrap; }

  .phone__lines { position: absolute; right: 16px; top: 128px; font-size: 15px; line-height: 1.65; white-space: nowrap; }

  .band { position: absolute; left: 54px; width: 772px; }
  .band--top { top: 57px; height: 90px; background: var(--band-dark); }
  .band--middle { top: 161px; height: 200px; background: var(--band-light); display: flex; align-items: center; justify-content: center; gap: 14px; }
  .band--bottom { top: 376px; height: 90px; background: var(--band-dark); }
  .band--middle .brand-name { color: var(--brand-blue); font-size: 40px; }
  .band--middle .brand-mark { background: var(--brand-blue); width: 20px; height: 20px; }
</style>
</head>
<body>
  <section class="card card--front" aria-label="Business card front">
    <div class="tile tile--dark tile--logo">
      <span class="brand-mark"></span>
      <span class="brand-name">Form Sculptors</span>
    </div>

    <div class="tile tile--blue tile--name">
      <svg class="tile__icon" viewBox="0 0 24 24" aria-hidden="true"><circle cx="12" cy="7.5" r="5"/><path d="M2 23c0-6 4.5-9 10-9s10 3 10 9z"/></svg>
      <p class="person__first">CALVERT</p>
      <p class="person__last">OSTERLUND</p>
    </div>

    <div class="tile tile--dark tile--title">
      <svg class="tile__icon tile__icon--stroke" viewBox="0 0 24 24" aria-hidden="true"><path d="M4 20l2-6L17 3l4 4-11 11z"/><path d="M14 6l4 4"/><path d="M3 22h9"/></svg>
      <p class="job-title">Chief<br>Executive</p>
    </div>

    <div class="tile tile--blue tile--info">
      <svg class="tile__icon" viewBox="0 0 24 24" aria-hidden="true"><path d="M1 3h22v14H1zM3 5v10h18V5z" fill-rule="evenodd"/><path d="M8 20h8v2H8z"/><path d="M11 17h2v3h-2z"/></svg>
      <p class="info__heading">INFO</p>
      <p class="info__lines">calvert@formsculptors-example.co.uk<br>www.formsculptors-example.co.uk</p>
    </div>

    <div class="tile tile--dark tile--address">
      <svg class="tile__icon" viewBox="0 0 24 24" aria-hidden="true"><path d="M12 2L1 12h3v10h6v-6h4v6h6V12h3z"/></svg>
      <p class="address__heading">FARROWMERE</p>
      <p class="address__lines">Clinic, London,<br>14 Farrowmere Lane</p>
    </div>

    <div class="tile tile--blue tile--phone">
      <svg class="tile__icon" viewBox="0 0 24 24" aria-hidden="true"><path d="M2 8c0-3 4-5 10-5s10 2 10 5v2h-5V8c-1-1-3-1.5-5-1.5S8 7 7 8v2H2z"/><path d="M6 11h12l3 10H3z"/><circle cx="12" cy="16" r="2.6" fill="#1f8bcf"/></svg>
      <p class="phone__lines">+44 (0)207 946 0321<br>+44 (0)7700 900 147</p>
    </div>
  </section>

  <section class="card card--back" aria-label="Business card back">
    <div class="band band--top"></div>
    <div class="band band--middle">
      <span class="brand-mark"></span>
      <span class="brand-name">Form Sculptors</span>
    </div>
    <div class="band band--bottom"></div>
  </section>
</body>
</html>
```